Plakat-Design für Immobilienmakler und Baufinanzierer
Zielgruppe
Wir sind Immobilienmakler und Baufinanzierer und suchen ein hochwertiges Design, unsere Zielgruppe sind Kunden, die Ihr Haus verkaufen möchten. Für jeden erfolgreichen Verkauf spenden wir 5 % unserer Maklercourtage an einen Verein, den sich der Kunde aussuchen darf. Mit diesem Plakat wollen wir auf unsere Vereinsförderng aufmerksam machen und Vereine ansprechen.
Aufgabenstellung
Text: 'Wir spenden 5 % unserer Provision für Ihren Verein', 'Nur 1,99 % Maklercourtage', Logo, Kontaktdaten

```html
<!DOCTYPE html>
<html lang="de">
<head>
<meta charset="utf-8">
<title>Hallstein Immobilien – Vereinsförderung</title>
<link href="https://fonts.googleapis.com/css2?family=Raleway:wght@400;500;700;800&display=swap" rel="stylesheet">
<style>
  :root {
    --teal: #0b6c7a;
    --teal-soft: #7db0c0;
    --wine: #8e1a2b;
    --text-grey: #555a5e;
    --paper: #ffffff;
    --photo-light: #c9d4e4;
    --photo-dark: #3d5a86;
  }
  html, body {
    margin: 0;
    padding: 0;
    width: 846px;
    height: 1200px;
    overflow: hidden;
    background: var(--paper);
  }
  .poster {
    position: relative;
    width: 846px;
    height: 1200px;
    background: var(--paper);
    font-family: 'Raleway', sans-serif;
  }
  .brand {
    position: absolute;
    right: 38px;
    top: 104px;
    font-family: 'Raleway', sans-serif;
    font-weight: 500;
    font-size: 23px;
    letter-spacing: 2px;
    color: var(--teal);
    text-transform: uppercase;
  }
  .photo-shadow {
    position: absolute;
    left: 53px;
    top: 200px;
    width: 760px;
    height: 477px;
    background: var(--teal-soft);
  }
  .photo {
    position: absolute;
    left: 36px;
    top: 187px;
    width: 759px;
    height: 473px;
    background: linear-gradient(100deg, #d8d6d3 0%, var(--photo-light) 35%, #b7c7de 60%, var(--photo-dark) 100%);
  }
  .price-badge {
    position: absolute;
    left: 55px;
    top: 104px;
    width: 240px;
    height: 240px;
    border-radius: 50%;
    background: var(--wine);
    color: var(--paper);
    display: flex;
    flex-direction: column;
    align-items: center;
    justify-content: center;
    text-align: center;
    font-size: 37px;
    line-height: 1.28;
  }
  .price-badge strong {
    font-weight: 800;
  }
  .headline {
    position: absolute;
    left: 36px;
    top: 742px;
    margin: 0;
    font-weight: 500;
    font-size: 41px;
    line-height: 50px;
    color: var(--teal);
  }
  .headline strong {
    font-weight: 800;
  }
  .steps {
    position: absolute;
    left: 36px;
    top: 880px;
    margin: 0;
    padding: 0;
    list-style: none;
  }
  .steps li {
    display: flex;
    align-items: center;
    height: 36px;
    margin-bottom: 28px;
    font-size: 21px;
    color: var(--text-grey);
  }
  .steps svg {
    width: 30px;
    height: 30px;
    margin-right: 26px;
    flex: none;
  }
  .footer {
    position: absolute;
    left: 0;
    bottom: 0;
    width: 846px;
    height: 63px;
    background: var(--teal);
    color: var(--paper);
    display: flex;
    align-items: center;
    justify-content: center;
    font-weight: 700;
    font-size: 23px;
  }
</style>
</head>
<body>
<div class="poster">
  <div class="brand">Hallstein Immobilien</div>

  <div class="photo-shadow"></div>
  <div class="photo" role="img" aria-label="Foto: Maklerin im gestreiften Hemd hält ein Klemmbrett mit einem kleinen weißen Hausmodell und einem Schlüsselbund"></div>

  <div class="price-badge">
    <span>Nur</span>
    <strong>1,99 %</strong>
    <span>Provision</span>
  </div>

  <h1 class="headline">Wir spenden 5 % unserer Provision<br>für <strong>Ihren Verein!</strong></h1>

  <ul class="steps">
    <li>
      <svg viewBox="0 0 30 30" aria-hidden="true"><path d="M25.5 12.5A11.5 11.5 0 1 1 19 4.6" fill="none" stroke="#0b6c7a" stroke-width="2.2" stroke-linecap="round"/><path d="M9 14.5l5 5L27 6" fill="none" stroke="#0b6c7a" stroke-width="2.2" stroke-linecap="round" stroke-linejoin="round"/></svg>
      Sie kennen jemanden, der eine Immobilie verkaufen möchte?
    </li>
    <li>
      <svg viewBox="0 0 30 30" aria-hidden="true"><path d="M25.5 12.5A11.5 11.5 0 1 1 19 4.6" fill="none" stroke="#0b6c7a" stroke-width="2.2" stroke-linecap="round"/><path d="M9 14.5l5 5L27 6" fill="none" stroke="#0b6c7a" stroke-width="2.2" stroke-linecap="round" stroke-linejoin="round"/></svg>
      Wir kümmern uns um den Verkauf und die gesamte Abwicklung.
    </li>
    <li>
      <svg viewBox="0 0 30 30" aria-hidden="true"><path d="M25.5 12.5A11.5 11.5 0 1 1 19 4.6" fill="none" stroke="#0b6c7a" stroke-width="2.2" stroke-linecap="round"/><path d="M9 14.5l5 5L27 6" fill="none" stroke="#0b6c7a" stroke-width="2.2" stroke-linecap="round" stroke-linejoin="round"/></svg>
      Nach Abschluss erhaltet Ihr Verein 5% unserer Provision!
    </li>
  </ul>

  <div class="footer">www.immobilien-hallstein.de</div>
</div>
</body>
</html>
```